High-end law practice specializing in closely held business succession planning and complex estates

Solo practitioner whose practice specializes in high-net worth, complex estate planning needs muliple versions of letterhead black and white, please. Letterhead should incorporate slogan, "Protecting your family business is my business," for one and "Complex Estate Planning"; third with no slogan. All for The Law Office of Marcy Lynn Pettibone, PC, 418 Cedar Hollow Ln., Newport News, Virginia 23648, Tel. 757-555-0142 Fax tbd email: marcy@mlplawgroup.example; Marcy Lynn Pettibone, Esq., principal, licensed in VA, NY, DC
Updates

Project Deadline Extended
Reason: My internet service went down and I can only view designs on my smart phone -- it's just too hard to review. So sorry! Working with my ISP now. Please be patient!

Target Market(s)

High net worth clients with complex estate planning needs, family businesses, family farmers, family foresters -- people with unique estate/succession planning needs who need a specialist who understands them.

Industry/Entity Type

Business

Font styles to use
Script

Requirements
Must have
• A high-end look and feel, connoting trustworthiness, special knowledge, and expertise.

```html
<!DOCTYPE html>
<html lang="en">
<head>
<meta charset="utf-8">
<title>The Law Office of Marcy Lynn Pettibone, PC — Stationery</title>
<link href="https://fonts.googleapis.com/css2?family=Crimson+Pro:wght@400;600&display=swap" rel="stylesheet">
<style>
  :root {
    --backdrop: #cfcfcf;
    --paper: #f0f0f0;
    --ink: #1e1e1e;
    --ink-soft: #444;
    --board: #262626;
    --board-edge: #1c1c1c;
    --silver: #c9c9c9;
    --silver-soft: #9a9a9a;
  }
  * { margin: 0; padding: 0; box-sizing: border-box; }
  html, body { width: 1200px; height: 1041px; overflow: hidden; }
  body {
    background: var(--backdrop);
    font-family: "Crimson Pro", Georgia, serif;
    color: var(--ink);
    position: relative;
  }
  .piece { position: absolute; }

  /* brand name lockup */
  .firm-name {
    text-transform: uppercase;
    font-weight: 400;
    line-height: 1.05;
    letter-spacing: 0.01em;
    display: flex;
    align-items: center;
    gap: 0.55em;
  }
  .firm-name .mark-square {
    width: 0.9em; height: 0.9em;
    border: 1px solid currentColor;
    flex: none;
  }

  /* presentation folder */
  .folder {
    left: 166px; top: 76px; width: 416px; height: 541px;
    background: var(--board);
    border-radius: 3px;
  }
  .folder .spine {
    position: absolute; left: 26px; top: 0; bottom: 0;
    width: 1px; background: var(--board-edge);
  }
  .folder .firm-name {
    position: absolute; left: 90px; top: 106px;
    font-size: 14px; color: var(--silver);
  }
  .folder .web {
    position: absolute; left: 0; right: 0; bottom: 43px;
    text-align: center; font-size: 8.5px; color: var(--silver);
  }

  /* letterhead */
  .letterhead {
    left: 615px; top: 95px; width: 402px; height: 522px;
    background: var(--paper);
  }
  .letterhead .firm-name {
    position: absolute; left: 26px; top: 34px; font-size: 8.5px;
  }
  .letterhead .contact {
    position: absolute; top: 32px; right: 32px;
    display: flex; font-size: 5px; line-height: 1.45; color: var(--ink-soft);
  }
  .contact .col { padding: 0 6px; border-left: 0.5px solid #999; }
  .contact .col:first-child { border-left: none; padding-left: 0; }
  .contact strong { font-weight: 600; color: var(--ink); }

  /* envelope front */
  .envelope-front {
    left: 132px; top: 646px; width: 451px; height: 194px;
    background: var(--paper);
  }
  .envelope-front .firm-name {
    position: absolute; left: 27px; top: 27px; font-size: 8px;
  }
  .envelope-front .return-address {
    position: absolute; left: 27px; top: 56px;
    font-size: 5px; line-height: 1.4; color: var(--ink-soft);
  }

  /* envelope back */
  .envelope-back {
    left: 615px; top: 646px; width: 451px; height: 194px;
    background: var(--paper);
  }
  .envelope-back svg { position: absolute; left: 0; top: 0; }
  .envelope-back .firm-name {
    position: absolute; left: 0; right: 0; top: 24px;
    justify-content: center; font-size: 6px; color: var(--silver-soft);
  }

  /* business cards */
  .card { top: 870px; width: 167px; height: 95px; }
  .card-front {
    left: 416px;
    background: linear-gradient(180deg, #2e2e2e, #222);
  }
  .card-front .firm-name {
    position: absolute; left: 0; right: 0; top: 40px;
    justify-content: center; font-size: 5.5px; color: var(--silver);
  }
  .card-front .web {
    position: absolute; left: 0; right: 0; bottom: 14px;
    text-align: center; font-size: 4px; color: var(--silver-soft);
  }
  .card-back { left: 615px; background: var(--paper); }
  .card-back .firm-name {
    position: absolute; left: 12px; top: 22px; font-size: 5.5px;
  }
  .card-back .details {
    position: absolute; left: 12px; bottom: 12px;
    font-size: 3.6px; line-height: 1.4; color: var(--ink-soft);
  }
  .card-back .principal {
    position: absolute; right: 12px; bottom: 16px; text-align: right;
    font-size: 3.6px; line-height: 1.4; color: var(--ink-soft);
  }
  .card-back .principal strong {
    font-size: 4.4px; font-weight: 600; color: var(--ink); text-transform: uppercase;
  }
</style>
</head>
<body>

  <section class="piece folder">
    <div class="spine"></div>
    <div class="firm-name"><span class="mark-square"></span><span>The Law Office<br>of Marcy Lynn Pettibone, PC</span></div>
    <p class="web">www.mlplawgroup.example</p>
  </section>

  <section class="piece letterhead">
    <div class="firm-name"><span class="mark-square"></span><span>The Law Office<br>of Marcy Lynn Pettibone, PC</span></div>
    <div class="contact">
      <div class="col"><strong>Marcy Lynn Pettibone</strong>, Esq.<br>Licensed in VA, NY, DC<br>E: marcy@mlplawgroup.example</div>
      <div class="col">T: 757-555-0142<br>F: 757-555-0199<br>www.mlplawgroup.example</div>
      <div class="col">418 Cedar Hollow Ln.<br>Newport News<br>Virginia 23648</div>
    </div>
  </section>

  <section class="piece envelope-front">
    <div class="firm-name"><span class="mark-square"></span><span>The Law Office<br>of Marcy Lynn Pettibone, PC</span></div>
    <p class="return-address">418 Cedar Hollow Ln.<br>Newport News<br>Virginia 23648</p>
  </section>

  <section class="piece envelope-back">
    <svg width="451" height="70" viewBox="0 0 451 70" aria-hidden="true">
      <path d="M0 0 H451 L432 58 Q430 64 424 64 H27 Q21 64 19 58 Z" fill="#262626"/>
    </svg>
    <div class="firm-name"><span class="mark-square"></span><span>The Law Office<br>of Marcy Lynn Pettibone, PC</span></div>
  </section>

  <section class="piece card card-front">
    <div class="firm-name"><span class="mark-square"></span><span>The Law Office<br>of Marcy Lynn Pettibone, PC</span></div>
    <p class="web">www.mlplawgroup.example</p>
  </section>

  <section class="piece card card-back">
    <div class="firm-name"><span class="mark-square"></span><span>The Law Office<br>of Marcy Lynn Pettibone, PC</span></div>
    <p class="details">418 Cedar Hollow Ln., Newport News, Virginia<br>T: 757-555-0142 · F: 757-555-0199<br>E: marcy@mlplawgroup.example</p>
    <p class="principal"><strong>Marcy Lynn Pettibone</strong>, Esq.<br>Licensed in VA, NY, DC</p>
  </section>

</body>
</html>
```